Ferncrest Roam Wording For Logo & Business card

I have the logo, I just need the "Ferncrest Roam" wording to go with it, and a business card design. The only thing on the business card is the website info. We provide nature connection experiences, and bolster these efforts through writing and host a platform for community around it.

I also have an idea of what it could look like (sketch), though I'm really not sure how it would come out. I am open to the best design and happy to consider original artwork. You can see what the site is about at FerncrestRoam.example.

Contact Information for Business Card

The only thing on the business card is the website info and the design. I will put other messaging on the back.

Website lettering (FerncrestRoam.example) in Montserrat

Logo Text

Ferncrest Roam (letters optional)

Font styles to use
Other font styles liked:
• montserrat

```html
<!DOCTYPE html>
<html lang="en">
<head>
<meta charset="utf-8">
<title>Ferncrest Roam — Business Card</title>
<link rel="stylesheet" href="https://fonts.googleapis.com/css2?family=Montserrat:wght@300;400;500&display=swap">
<style>
  :root {
    --page-bg: #e4e4e6;
    --card-deep: #0d0624;
    --card-mid: #1d1236;
    --accent-orange: #f08a1c;
    --accent-amber: #ffc93a;
    --ember-purple: #6c4a86;
    --text-light: #f2f0f5;
    --text-silver: #c9c8d2;
    --card-w: 520px;
    --card-h: 297px;
  }
  * { box-sizing: border-box; margin: 0; padding: 0; }
  html, body { width: 1200px; height: 800px; overflow: hidden; }
  body {
    background: var(--page-bg);
    font-family: "Montserrat", sans-serif;
    display: flex;
    align-items: center;
    justify-content: center;
    gap: 56px;
  }
  .card {
    position: relative;
    width: var(--card-w);
    height: var(--card-h);
    border-radius: 18px;
    overflow: hidden;
    background: linear-gradient(135deg, var(--card-mid) 0%, var(--card-deep) 70%);
    box-shadow: 0 10px 26px rgba(0,0,0,.25);
  }

  /* Front side */
  .artwork-area {
    position: absolute;
    left: -40px;
    bottom: -60px;
    width: 300px;
    height: 300px;
    border-radius: 50%;
    background: radial-gradient(circle at 55% 50%, var(--accent-amber) 0%, var(--accent-orange) 32%, var(--ember-purple) 62%, rgba(29,18,54,0) 75%);
  }
  .website-block {
    position: absolute;
    right: 38px;
    top: 72px;
    display: flex;
    align-items: center;
    gap: 8px;
    font-size: 13px;
    font-weight: 300;
    color: var(--text-light);
  }
  .web-icon { width: 12px; height: 12px; }

  /* Brand side */
  .brand-row {
    position: absolute;
    left: 44px;
    right: 30px;
    top: 106px;
    display: flex;
    align-items: center;
    gap: 20px;
  }
  .brand-dot {
    flex: none;
    width: 38px; height: 38px; border-radius: 50%;
    background: var(--accent-orange);
  }
  .brand-name {
    font-size: 30px;
    font-weight: 300;
    letter-spacing: 4px;
    text-transform: uppercase;
    color: var(--text-silver);
    white-space: nowrap;
  }
  .web-row {
    position: absolute;
    left: 24px; right: 24px;
    bottom: 70px;
    display: flex;
    align-items: center;
    gap: 12px;
  }
  .divider-line {
    flex: 1;
    height: 1px;
    background: var(--accent-orange);
    opacity: .8;
  }
  .web-address {
    font-size: 15px;
    font-weight: 400;
    letter-spacing: 1px;
    color: var(--text-light);
    white-space: nowrap;
  }
</style>
</head>
<body>

  <section class="card card-front">
    <div class="artwork-area" role="img" aria-label="Warm decorative artwork area in orange and amber on purple"></div>
    <p class="website-block">ferncrestroam.example
      <svg class="web-icon" viewBox="0 0 12 12" aria-hidden="true"><circle cx="6" cy="6" r="5" fill="#f08a1c"/><path d="M1 6h10M6 1c-2 3-2 7 0 10M6 1c2 3 2 7 0 10" stroke="#0d0624" stroke-width=".8" fill="none"/></svg>
    </p>
  </section>

  <section class="card card-brand">
    <div class="brand-row">
      <span class="brand-dot" aria-hidden="true"></span>
      <span class="brand-name">Ferncrest Roam</span>
    </div>
    <div class="web-row">
      <span class="divider-line" aria-hidden="true"></span>
      <span class="web-address">www.FerncrestRoam.example</span>
      <span class="divider-line" aria-hidden="true"></span>
    </div>
  </section>

</body>
</html>
```